Meridale Partners Website

Meridale Partners (MP) provide Analytics & Enterprise Performance Management (EPM) advisory & consultancy services. We are passionate about data and making a difference for our clients by working in partnership with them, helping them on their journey to becoming an Meridale Partner. We deliver insights which give our clients a competitive edge and a much deeper understanding of their organisation.

We need a website which shows who we are, what we do and how we do it.

www.meridale-partners.example is our very basic website at the moment. We want to completely revamp it with a corporate look

```html
<!DOCTYPE html>
<html lang="en">
<head>
<meta charset="utf-8">
<title>Meridale Partners</title>
<link rel="stylesheet" href="https://fonts.googleapis.com/css2?family=Montserrat:wght@600;700;800&family=Roboto:wght@400;500;700&family=Mulish:wght@400;600&display=swap">
<style>
:root{
  --teal:#2b5370;
  --teal-deep:#1f425c;
  --teal-mid:#3b6a8a;
  --orange:#d9823f;
  --ink:#111;
  --grey:#6b6b6b;
  --white:#fff;
  --black:#000;
}
*{margin:0;padding:0;box-sizing:border-box}
html,body{width:1200px;height:3196px;overflow:hidden;background:var(--white)}
body{position:relative;font-family:'Roboto',sans-serif;color:var(--ink)}
.abs{position:absolute}
.heading{font-family:'Montserrat',sans-serif;font-weight:700}
.body-copy{font-family:'Mulish',sans-serif;color:var(--grey)}
.btn{position:absolute;border:2px solid currentColor;border-radius:24px;font-family:'Roboto',sans-serif;font-weight:700;font-size:14px;display:flex;align-items:center;justify-content:center;gap:6px;text-transform:uppercase}
.btn .arrow{width:12px;height:12px;border-radius:50%;background:currentColor;position:relative}
.btn .arrow::after{content:"";position:absolute;left:3px;top:3px;width:4px;height:4px;border-right:2px solid var(--white);border-top:2px solid var(--white);transform:rotate(45deg)}
.btn.dark .arrow::after{border-color:var(--white)}
.logo{position:absolute;display:flex;align-items:center;gap:14px;color:var(--white)}
.logo .mark{border-radius:50%;border:7px solid var(--white)}
.logo .name{font-family:'Montserrat',sans-serif;font-weight:700;line-height:1.05;text-transform:uppercase}

/* hero */
.hero{position:absolute;left:0;top:0;width:1200px;height:686px;background:linear-gradient(100deg,#1d4a66 0%,#2c5d7c 45%,#476f86 70%,#2a4f68 100%)}
.nav{position:absolute;top:48px;left:577px;display:flex;gap:33px;font-weight:700;font-size:14px;color:var(--white)}
.nav .active{border-bottom:2px solid var(--white);padding-bottom:6px}
.hero-title{left:108px;top:226px;font-size:62px;line-height:68px;color:var(--white)}
.hero-sub{left:110px;top:380px;font-size:17px;line-height:26px;color:var(--white);font-family:'Montserrat',sans-serif;font-weight:700}
.dots{left:112px;top:601px;display:flex;gap:8px}
.dots span{width:13px;height:13px;border-radius:50%;background:var(--white)}

/* who */
.who-photo{left:152px;top:790px;width:410px;height:410px;border-radius:50%;background:radial-gradient(circle at 55% 40%,#dfe6ec 0%,#9fb4c5 45%,#2f5f82 80%,#1f3f58 100%)}
.eyebrow{left:601px;top:785px;font-size:17px;color:var(--teal);font-family:'Montserrat',sans-serif;font-weight:700}
.who-title{left:600px;top:815px;font-size:42px;color:var(--black)}
.rule{position:absolute;height:3px;background:var(--teal)}
.who-text{left:601px;top:896px;width:470px;font-size:14.5px;line-height:25.6px}
.contact-row{position:absolute;left:600px;display:flex;align-items:center;gap:12px}
.contact-row .ic{width:46px;height:46px;border-radius:50%;background:var(--teal);display:flex;align-items:center;justify-content:center}
.contact-row .lbl{font-weight:700;font-size:14px;color:var(--ink)}
.contact-row .val{font-weight:500;font-size:21px;color:var(--teal)}

/* what */
.what-band{left:0;top:1299px;width:1200px;height:342px;background:linear-gradient(180deg,#2b5370,#2f5a78)}
.section-title{position:absolute;width:1200px;text-align:center;font-size:43px}
.card-img{position:absolute;top:1498px;width:310px;height:236px;border-radius:0 0 40px 0}
.card-title{position:absolute;width:310px;text-align:center;top:1758px;font-size:19px;color:var(--teal);font-family:'Montserrat',sans-serif;font-weight:700}
.card-text{position:absolute;width:290px;text-align:center;top:1790px;font-size:14.5px;line-height:25.6px}

/* how */
.step{position:absolute;width:190px;text-align:center}
.step h3{font-family:'Roboto',sans-serif;font-weight:500;font-size:18px;line-height:26px;color:var(--teal)}
.step .mini{width:36px;height:2px;background:var(--teal);margin:12px auto 12px}
.step p{font-family:'Mulish',sans-serif;font-size:14px;line-height:25.6px;color:var(--grey)}

/* cta */
.footer-band{left:0;top:2677px;width:1200px;height:519px;background:var(--black)}
.cta{left:112px;top:2512px;width:976px;height:296px;background:var(--teal)}
.cta-photo{left:116px;top:2516px;width:280px;height:288px;background:linear-gradient(135deg,#c9ccd0,#7d8791 55%,#3b4148)}
.cta-title{left:439px;top:2552px;font-size:45px;line-height:50px;color:var(--white)}
.cta-sub{left:444px;top:2672px;font-size:15px;color:var(--orange);font-family:'Montserrat',sans-serif;font-weight:700}

/* footer */
.foot-h{position:absolute;top:2880px;font-family:'Roboto',sans-serif;font-weight:700;font-size:20px;color:var(--white)}
.foot-list{position:absolute;font-size:14px;line-height:26px;color:var(--white)}
.foot-list li{list-style:none;position:relative;padding-left:36px}
.links li::before{content:"»";position:absolute;left:0;color:var(--orange);font-weight:700}
.partner{left:560px;top:2978px;display:flex;align-items:center;gap:12px;color:var(--white);font-size:14px}
.partner .sq{width:72px;height:12px;background:#c74634}
.partner .div{width:1px;height:34px;background:#888}
.socials{left:547px;top:3023px;display:flex;gap:8px}
.socials span{width:38px;height:38px;border:2px solid var(--white);border-radius:50%}
.copy{left:0;top:3120px;width:1200px;text-align:center;font-size:14px;color:var(--white)}
</style>
</head>
<body>

<!-- Hero -->
<section class="hero" role="img" aria-label="Photo of two business colleagues reviewing a tablet in an office"></section>
<div class="logo" style="left:110px;top:20px">
  <span class="mark" style="width:66px;height:66px"></span>
  <span class="name" style="font-size:24px">Meridale<br>Partners</span>
</div>
<nav class="nav"><span class="active">Home</span><span>Services</span><span>About Us</span><span>Contact Us</span></nav>
<div class="btn" style="left:936px;top:34px;width:153px;height:44px;color:var(--white)">Get a quote</div>
<h1 class="abs heading hero-title">Meridale<br>Partners</h1>
<p class="abs hero-sub">DATA ANALYTICS &amp; EPM CONSULTING<br>SERVICES</p>
<div class="btn" style="left:112px;top:454px;width:152px;height:44px;color:var(--white)">Get started <span class="arrow" style="background:var(--white)"></span></div>
<div class="abs dots"><span></span><span></span><span></span><span></span></div>

<!-- Who we are -->
<div class="abs who-photo" role="img" aria-label="Photo of two consultants working on a laptop, framed in a circle"></div>
<p class="abs eyebrow">MERIDALE PARTNERS</p>
<h2 class="abs heading who-title">WHO WE ARE</h2>
<div class="rule" style="left:601px;top:878px;width:66px"></div>
<p class="abs body-copy who-text">Meridale Partners is an exciting start-up in the Data Analytics and EPM space.&nbsp; Founded in 2019, MP specialise in the implementation and support of BI, EPM and Data Analytics business solutions, both in the Cloud and on-premise.</p>
<div class="btn dark" style="left:601px;top:1018px;width:152px;height:44px;color:var(--teal)">Learn more <span class="arrow"></span></div>
<div class="contact-row" style="top:1086px">
  <span class="ic"><svg width="16" height="16" viewBox="0 0 24 24"><path fill="#fff" d="M6.6 10.8a15 15 0 006.6 6.6l2.2-2.2c.3-.3.7-.4 1-.2 1.1.4 2.3.6 3.6.6.6 0 1 .4 1 1V20c0 .6-.4 1-1 1A17 17 0 013 4c0-.6.4-1 1-1h3.5c.6 0 1 .4 1 1 0 1.3.2 2.5.6 3.6.1.3 0 .7-.2 1z"/></svg></span>
  <span class="lbl">Call us :</span><span class="val">01 555 0142</span>
</div>
<div class="contact-row" style="top:1150px">
  <span class="ic"><svg width="16" height="12" viewBox="0 0 16 12"><rect width="16" height="12" rx="1" fill="#fff"/><path d="M0 1l8 6 8-6" stroke="#2b5370" stroke-width="1.6" fill="none"/></svg></span>
  <span class="lbl">Email us :</span><span class="val">info@meridale-partners.example</span>
</div>

<!-- What we do -->
<div class="abs what-band"></div>
<h2 class="heading section-title" style="top:1388px;color:var(--white)">WHAT WE DO</h2>
<div class="rule" style="left:567px;top:1453px;width:66px;background:var(--white)"></div>

<div class="card-img" style="left:112px;background:linear-gradient(135deg,#d9d4cc,#9aa3ab 60%,#4d5a66)" role="img" aria-label="Photo of two colleagues discussing a document at a desk"></div>
<div class="card-img" style="left:445px;background:linear-gradient(135deg,#6e6a62,#b9b5a8 50%,#e4e1d6)" role="img" aria-label="Photo of charts and notes spread on a desk"></div>
<div class="card-img" style="left:778px;background:linear-gradient(135deg,#e7e8ea,#a9b3bc 55%,#3f4e5c)" role="img" aria-label="Photo of a team gathered around a laptop"></div>

<h3 class="card-title" style="left:112px">ADVISE &amp; ARCHITECT</h3>
<h3 class="card-title" style="left:445px">DESIGN &amp; IMPLEMENT</h3>
<h3 class="card-title" style="left:778px">OPTIMISE &amp; MANAGE</h3>
<p class="card-text body-copy" style="left:122px">Helping our customers understand the art of the possible and safeguarding their investments by overseeing implementations.</p>
<p class="card-text body-copy" style="left:455px">Working with the project management team, through each stage of the project, with clearly defined deliverables and well exercised plans to deliver them.</p>
<p class="card-text body-copy" style="left:788px">Helping our customers understand the art of the possible and safeguarding their investments by overseeing implementations.</p>
<div class="btn dark" style="left:192px;top:1912px;width:152px;height:44px;color:var(--teal)">Learn more <span class="arrow"></span></div>
<div class="btn dark" style="left:525px;top:1912px;width:152px;height:44px;color:var(--teal)">Learn more <span class="arrow"></span></div>
<div class="btn dark" style="left:858px;top:1912px;width:152px;height:44px;color:var(--teal)">Learn more <span class="arrow"></span></div>

<!-- How we do it -->
<h2 class="heading section-title" style="top:2047px;color:var(--black)">HOW WE DO IT</h2>
<div class="rule" style="left:551px;top:2113px;width:98px"></div>
<svg class="abs" style="left:0;top:0" width="1200" height="2420" viewBox="0 0 1200 2420" aria-hidden="true">
  <defs>
    <linearGradient id="wave" gradientUnits="userSpaceOnUse" x1="0" y1="2162" x2="0" y2="2400">
      <stop offset="0" stop-color="#d9823f"/>
      <stop offset="1" stop-color="#3a5870"/>
    </linearGradient>
  </defs>
  <g fill="none" stroke="url(#wave)" stroke-width="4">
    <path d="M290 2193 A117 117 0 1 0 320 2330"/>
    <path d="M320 2330 C340 2280 345 2240 365 2215 A117 117 0 0 1 575 2225"/>
    <path d="M365 2330 A117 117 0 0 0 590 2310"/>
    <path d="M590 2310 C600 2270 610 2240 625 2215 A117 117 0 0 1 832 2225"/>
    <path d="M623 2330 A117 117 0 0 0 850 2310"/>
    <path d="M850 2310 C860 2270 870 2240 885 2215 A117 117 0 1 1 910 2370"/>
  </g>
  <g fill="#d9823f">
    <circle cx="290" cy="2193" r="7"/><circle cx="575" cy="2225" r="7"/><circle cx="832" cy="2225" r="7"/>
  </g>
  <g fill="#3a5870">
    <circle cx="365" cy="2330" r="7"/><circle cx="623" cy="2330" r="7"/><circle cx="910" cy="2370" r="7"/>
  </g>
</svg>
<div class="step" style="left:118px;top:2222px"><h3>Analytics</h3><div class="mini"></div><p>Lorem ipsum dolor sit amet, consectetur adipiscing elit, sed do</p></div>
<div class="step" style="left:383px;top:2196px"><h3>Enterprise Performance Management</h3><div class="mini"></div><p>Lorem ipsum dolor sit amet, consectetur adipiscing elit, sed do</p></div>
<div class="step" style="left:633px;top:2222px"><h3>Advisory</h3><div class="mini"></div><p>Lorem ipsum dolor sit amet, consectetur adipiscing elit, sed do</p></div>
<div class="step" style="left:896px;top:2222px"><h3>Consultancy</h3><div class="mini"></div><p>Lorem ipsum dolor sit amet, consectetur adipiscing elit, sed do</p></div>

<!-- CTA + Footer -->
<div class="abs footer-band"></div>
<div class="abs cta"></div>
<div class="abs cta-photo" role="img" aria-label="Photo of two business people shaking hands across a desk"></div>
<h2 class="abs heading cta-title">CONTACT US TO DISCUSS<br>YOUR BUSINESS NEEDS</h2>
<p class="abs cta-sub">ADVISE &amp; ARCHITECT | DESIGN &amp; IMPLEMENT | OPTIMISE &amp; MANAGE</p>
<div class="btn" style="left:444px;top:2712px;width:153px;height:44px;color:var(--white)">
  <svg width="12" height="12" viewBox="0 0 24 24"><path fill="#fff" d="M6.6 10.8a15 15 0 006.6 6.6l2.2-2.2c.3-.3.7-.4 1-.2 1.1.4 2.3.6 3.6.6.6 0 1 .4 1 1V20c0 .6-.4 1-1 1A17 17 0 013 4c0-.6.4-1 1-1h3.5c.6 0 1 .4 1 1 0 1.3.2 2.5.6 3.6.1.3 0 .7-.2 1z"/></svg>
  Contact us
</div>

<h4 class="foot-h" style="left:110px">CONTACT US</h4>
<ul class="foot-list" style="left:110px;top:2920px">
  <li><svg class="abs" style="left:2px;top:6px" width="10" height="14" viewBox="0 0 10 14"><path fill="#d9823f" d="M5 0a5 5 0 015 5c0 4-5 9-5 9S0 9 0 5a5 5 0 015-5z"/><circle cx="5" cy="5" r="2" fill="#000"/></svg>12 Harbour Row,<br>Quayside, Dublin 4,<br>D04 XK21</li>
  <li><svg class="abs" style="left:1px;top:7px" width="12" height="12" viewBox="0 0 24 24"><path fill="#d9823f" d="M6.6 10.8a15 15 0 006.6 6.6l2.2-2.2c.3-.3.7-.4 1-.2 1.1.4 2.3.6 3.6.6.6 0 1 .4 1 1V20c0 .6-.4 1-1 1A17 17 0 013 4c0-.6.4-1 1-1h3.5c.6 0 1 .4 1 1 0 1.3.2 2.5.6 3.6.1.3 0 .7-.2 1z"/></svg>01 555 0142</li>
  <li><svg class="abs" style="left:0;top:8px" width="14" height="10" viewBox="0 0 16 12"><rect width="16" height="12" rx="1" fill="#d9823f"/><path d="M0 1l8 6 8-6" stroke="#000" stroke-width="1.6" fill="none"/></svg>info@meridale-partners.example</li>
</ul>

<div class="logo" style="left:484px;top:2870px">
  <span class="mark" style="width:80px;height:80px;border-width:8px"></span>
  <span class="name" style="font-size:28px">Meridale<br>Partners</span>
</div>
<div class="abs partner"><span class="sq"></span><span class="div"></span><span>Partner</span></div>
<div class="abs socials"><span></span><span></span><span></span><span></span></div>

<h4 class="foot-h" style="left:955px">QUICK LINKS</h4>
<ul class="foot-list links" style="left:957px;top:2920px">
  <li>Home</li><li>About us</li><li>Services</li><li>Blog</li><li>Faq</li><li>Contact us</li>
</ul>

<p class="abs copy">© Copyrights 2022 The Company Name.All Rights Reserved</p>
</body>
</html>
```